Construction material supplies company business card ****

1. Full company name “K T Masonry Works Ltd”
I am after a Business card design for the company as a whole. We are better known in Solomon Islands as “K T Masonry” for short.

We are a building materials supplier of
Ready Mixed Concrete, Bricks and Blocks,
Quarry products- gravel, aggregates, sand etc.
Cement distributor/retailer of reputable brands.
Other prefab concrete products. Culverts, wave breakers, concrete retaining blocks etc.

2. Competitive Advantage over Competition: Quality, efficient, professional, dependable, reliable

3. We want people to feel trust worthy, high quality, strong when they see our brand

5. No preference to color. Maybe more sturdy and corporate. Not fancy.

Industry/Entity Type

CONSTRUCTION SUPPLY

Contact Information for Business Card

Name, Position, office phone mob phone, email

Requirements
Must have
• the company logo
Nice to have
• would like to see a mixture of designs, of with logo only and also with simple graphic designs to bring out the company whilst still have the strong sturdy professional feeling

```html
<!DOCTYPE html>
<html lang="en">
<head>
<meta charset="UTF-8">
<title>K T Masonry – Business Card</title>
<link href="https://fonts.googleapis.com/css2?family=Roboto:wght@400;500;700&display=swap" rel="stylesheet">
<style>
  :root {
    --backdrop: #2a2a2a;
    --concrete-light: #e6e6e6;
    --concrete-mid: #d3d3d3;
    --navy: #163f66;
    --white: #ffffff;
    --shadow: rgba(0,0,0,0.45);
  }
  * { margin: 0; padding: 0; box-sizing: border-box; }
  html, body {
    width: 1200px; height: 1138px; overflow: hidden;
    background: var(--backdrop);
    font-family: 'Roboto', sans-serif;
    color: var(--navy);
  }
  .card {
    position: absolute;
    width: 620px; height: 374px;
    border-radius: 14px;
    background: radial-gradient(ellipse at 40% 35%, var(--concrete-light), var(--concrete-mid));
    box-shadow: 0 6px 14px var(--shadow);
    overflow: hidden;
  }
  .card--front { left: 274px; top: 186px; }
  .card--back { left: 276px; top: 608px; }

  .front-name {
    position: absolute; left: 0; right: 0; top: 150px;
    text-align: center;
    font-size: 44px; font-weight: 700;
    color: var(--navy);
  }
  .front-web {
    position: absolute; left: 0; right: 0; bottom: 24px;
    text-align: center;
    font-size: 16px; font-weight: 500;
    letter-spacing: 6px;
  }

  .wave { position: absolute; left: 0; top: 0; }
  .tagline {
    position: absolute; right: 36px; top: 22px;
    text-align: right;
    color: var(--white);
    font-size: 16.5px; line-height: 24px;
  }
  .brand-name {
    position: absolute; left: 36px; top: 196px;
    font-size: 32px; font-weight: 700;
    color: var(--navy);
  }
  .person { position: absolute; left: 36px; top: 284px; }
  .person-name { font-size: 23px; font-weight: 700; }
  .person-role { font-size: 16px; margin-top: 2px; }

  .address {
    position: absolute; right: 36px; top: 200px;
    text-align: right;
    font-size: 16px; line-height: 26px;
  }
  .contacts {
    position: absolute; right: 36px; top: 268px;
    list-style: none;
    font-size: 16px;
  }
  .contacts li {
    display: flex; justify-content: flex-end; align-items: center;
    height: 26px;
  }
  .contacts svg { width: 14px; height: 14px; margin-left: 12px; fill: var(--navy); }
</style>
</head>
<body>

<section class="card card--front">
  <div class="front-name">K T Masonry</div>
  <div class="front-web">www.ktmasonry.com</div>
</section>

<section class="card card--back">
  <svg class="wave" width="620" height="374" viewBox="0 0 620 374" aria-hidden="true">
    <path d="M0,44 C60,20 130,6 200,0 L620,0 L620,112 C560,132 490,122 410,84 C290,24 140,22 0,70 Z" fill="#163f66"/>
    <path d="M70,58 C170,20 290,22 370,56" fill="none" stroke="#e0e0e0" stroke-width="4" stroke-linecap="round"/>
  </svg>

  <div class="tagline">
    Quality &nbsp;|&nbsp; Efficient<br>
    Dependable &nbsp;|&nbsp; Reliable<br>
    Professional
  </div>

  <div class="brand-name">K T Masonry</div>

  <div class="person">
    <div class="person-name">Daniel Harper</div>
    <div class="person-role">Managing Director</div>
  </div>

  <div class="address">
    48 Kukum Highway, Honiara,<br>
    Solomon Islands
  </div>

  <ul class="contacts">
    <li>000 0000 0000
      <svg viewBox="0 0 16 16"><path d="M3 2h3l1.5 3.5-2 1.2a8 8 0 0 0 3.8 3.8l1.2-2L14 10v3a1 1 0 0 1-1 1A11 11 0 0 1 2 3a1 1 0 0 1 1-1z"/></svg>
    </li>
    <li>daniel@ktmasonry.com
      <svg viewBox="0 0 16 16"><path d="M1 3h14v10H1z M1.5 3.5 8 9l6.5-5.5" fill="none" stroke="#163f66" stroke-width="1.6"/></svg>
    </li>
    <li>www.ktmasonry.com
      <svg viewBox="0 0 16 16"><circle cx="8" cy="8" r="6.5" fill="none" stroke="#163f66" stroke-width="1.4"/><path d="M1.5 8h13M8 1.5c-3 3.5-3 9.5 0 13M8 1.5c3 3.5 3 9.5 0 13" fill="none" stroke="#163f66" stroke-width="1.2"/></svg>
    </li>
  </ul>
</section>

</body>
</html>
```